Web site for small printshop

I am looking for a website for small printshop in Iceland, mainly serving university students and artist.

We print posters, flyers, business cards and more.

In addition to our current website, I would like to include design tool, (fx. www.quarvelpad.example, www.trindomap.example or something similar) jobs upload, shopping chart.
Updates

Great work, I am really amazed of the quality of work i am seeing here.

Really way beyond my expectation

GOOD JOB - all of you ! 

Hi all.

The designs submitted have been great, way better than expected.
I really did not expect this level of quality.

Some have been asking me for feedback on their designs, and I will try 
to send some feedback here, without spoiling your creativity.

Likes:
- when the colors of my logo is used in menus, buttons etc.
- simple, not to crowded look.

Dislikes.
- Dark and heavy design
- Lot of text and buttons (crowded look)

Extra info.
- top line (before menus) will contain: Tel - email - language
- menu line will have 5 categories: Home - service - submission of works - FAQ - about us
- 3 large buttons:  Job submit - Job design - ask for offer

LOVE YOUR WORK - great designs so far :)

Target Market(s)

University Students, Artists. Age group 20-30

Industry/Entity Type

University

Requirements
Must have
• The website must be easy to use, clean looking.

```html
<!DOCTYPE html>
<html lang="en">
<head>
<meta charset="utf-8">
<title>Kjarni Studio – Print Shop</title>
<link rel="stylesheet" href="https://fonts.googleapis.com/css2?family=Arimo:wght@400;700&family=Questrial&display=swap">
<style>
:root{
  --paper:#f2f1ec;
  --yellow:#f7de4f;
  --yellow-light:#f5e46f;
  --green:#0e6331;
  --red:#e8393b;
  --ink:#1e1e1e;
  --rule:#dedcd5;
  --white:#ffffff;
}
*{box-sizing:border-box;margin:0;padding:0}
html,body{width:882px;height:1200px;overflow:hidden}
body{background:var(--paper);font-family:"Arimo",Arial,sans-serif;color:var(--ink);position:relative}
h1,h2,h3{font-weight:400}
.abs{position:absolute}

/* top bar */
.topbar{left:0;top:0;width:882px;height:76px;background:linear-gradient(180deg,var(--yellow-light),var(--yellow))}
.brand{left:75px;top:34px;font-family:"Questrial",sans-serif;font-weight:400;font-size:16px;color:#3a3a3a;letter-spacing:.3px}
.main-nav a{position:absolute;top:36px;font-weight:700;font-size:15px;color:#111;text-decoration:none;transform:translateX(-50%);white-space:nowrap}
.main-nav .active{left:279px;top:0;width:99px;height:83px;background:var(--green);transform:none}
.main-nav .active span{position:absolute;left:0;right:0;top:36px;text-align:center;color:var(--white)}

/* hero */
.hero{left:0;top:76px;width:882px;height:270px;background:
  radial-gradient(ellipse 260px 130px at 360px 150px,#4fc6cf 0%,rgba(79,198,207,.35) 45%,rgba(220,228,230,0) 80%),
  radial-gradient(ellipse 220px 90px at 420px 210px,#e6e9ec 0%,rgba(230,233,236,0) 80%),
  linear-gradient(90deg,#cfdde3 0%,#e7ecee 40%,#f0f0ec 70%,#eeeeea 100%)}
.hero-title{left:605px;top:202px;font-family:"Arimo",sans-serif;font-weight:400;font-size:30px;line-height:1;letter-spacing:.3px}
.hero-title .red{color:var(--red)}
.hero-title .green{color:var(--green)}
.hero-title .small{font-size:15px;color:#111;letter-spacing:.8px}
.hero-title .line2{display:block;margin-top:2px;padding-left:52px}

/* sub nav */
.sub-nav{left:131px;top:360px;width:584px;height:40px;border-bottom:1px solid var(--rule);font-family:"Questrial",sans-serif;font-size:13px}
.sub-nav span{position:absolute;top:8px;white-space:nowrap;letter-spacing:.3px}
.sub-nav svg{position:absolute;left:38px;top:3px}

.heading{font-family:"Questrial",sans-serif;font-size:18px;font-weight:400;letter-spacing:.5px}
.section-title{left:131px;width:584px;text-align:center;color:var(--green);font-size:18px}
.rule{left:131px;width:584px;height:1px;background:var(--rule)}
.copy{font-size:9.4px;line-height:15.2px;letter-spacing:.1px;color:#222}

.story-heading{left:131px;top:419px}
.story-media{left:190px;top:448px;width:95px;height:105px;background:linear-gradient(135deg,#bdbdbd,#2c2c2c 55%,#d36a1e);transform:rotate(-12deg);border:4px solid #eaeaea;box-shadow:0 2px 4px rgba(0,0,0,.35)}
.story-copy{left:314px;top:463px;width:380px}

/* steps */
.step-u{left:168px;top:692px;font-family:"Arimo",sans-serif;font-weight:700;font-size:60px;color:var(--red);line-height:1}
.step-upload{left:219px;top:693px;font-family:"Questrial",sans-serif;font-size:12px;line-height:1}
.step-upload small{display:block;font-family:Georgia,serif;font-size:8px;color:#777;margin-top:2px;letter-spacing:.3px}
.step-size{left:327px;top:690px;font-family:"Questrial",sans-serif;font-size:18px}
.step-size em{font-style:normal;color:var(--red);font-size:13px}
.size-select{left:327px;top:718px;width:141px;height:28px;background:#f7f6f2;border:1px solid #cfcdc6;font-size:10px;color:#444;text-align:center;line-height:26px}
.size-select svg{position:absolute;right:10px;top:10px}
.step-pay{left:514px;top:733px;font-family:"Questrial",sans-serif;font-size:12.5px;letter-spacing:.3px}

/* printer card */
.corner-dark{left:137px;top:850px;width:52px;height:59px;background:#232323}
.corner-red{left:692px;top:1025px;width:53px;height:58px;background:var(--red)}
.card{left:153px;top:866px;width:576px;height:202px;background:var(--white);box-shadow:0 1px 4px rgba(0,0,0,.12)}
.printer-media{left:32px;top:28px;width:153px;height:148px;border-radius:6px;background:linear-gradient(170deg,#e9eef0 0%,#9aa3a8 40%,#2b7fd0 65%,#1b1f24 85%)}
.card-heading{left:216px;top:38px}
.card-copy{left:214px;top:82px;width:322px}

.footer-rule{left:353px;top:1139px;width:199px;height:1px;background:var(--rule)}
.footer{left:0;top:1160px;width:882px;text-align:center;font-size:7px;font-weight:700;letter-spacing:.2px}
.footer .red{color:var(--red)}
</style>
</head>
<body>

<header class="abs topbar"></header>
<div class="abs brand">Kjarni Studio</div>
<nav class="main-nav">
  <a class="active" href="#"><span>HOME</span></a>
  <a href="#" style="left:442px">ABOUT US</a>
  <a href="#" style="left:562px">PORTOFOLIO</a>
  <a href="#" style="left:693px">CONTACT US</a>
</nav>

<section class="abs hero" role="img" aria-label="Young man jumping through splashes of turquoise, white and orange paint"></section>
<h1 class="abs hero-title">
  <span class="red">WORLD</span><span class="green">OF</span>
  <span class="line2"><span class="small">REAL</span> <span class="red">COLORS</span></span>
</h1>

<nav class="abs sub-nav">
  <svg width="20" height="18" viewBox="0 0 20 18" aria-hidden="true"><path d="M10 1 L19 9 H16 V17 H12 V12 H8 V17 H4 V9 H1 Z" fill="#e8393b"/></svg>
  <span style="left:77px">HOME</span>
  <span style="left:169px">CATOGOREY</span>
  <span style="left:320px">ABOUT US</span>
  <span style="left:443px">BUY ONLINE</span>
</nav>

<h2 class="abs heading story-heading">STORY BOARD</h2>
<div class="abs story-media" role="img" aria-label="Photo frame icon showing a paint brush with orange paint"></div>
<p class="abs copy story-copy">Crumb Corner sprouted from a hot dog cart in Linden Row Park in Eastvale created by Tomas Revel's Harbor Lane Hospitality Group (HLHG) to support the Linden Row Park Conservancy's first art installation. The cart was quite the success, with Crumb Fans lined up daily for three summers.</p>

<div class="abs rule" style="top:566px"></div>
<h2 class="abs heading section-title" style="top:586px">HOW CAN YOU CONTACT US</h2>
<div class="abs rule" style="top:625px"></div>

<div class="abs step-u">U</div>
<div class="abs step-upload">PLOAD<small>YOUR FILES</small></div>
<svg class="abs" style="left:238px;top:713px" width="72" height="34" viewBox="0 0 72 34" aria-hidden="true">
  <path d="M2 11 H44 V3 L70 17 L44 31 V23 H2 Z" fill="none" stroke="#222" stroke-width="2.2" stroke-linejoin="round"/>
  <path d="M10 12 V22 M18 12 V22 M26 12 V22 M34 12 V22" stroke="#222" stroke-width="2.5"/>
</svg>
<div class="abs step-size">SELECT <em>THE SIZE</em></div>
<div class="abs size-select">A3
  <svg width="10" height="7" viewBox="0 0 10 7" aria-hidden="true"><path d="M1 1 L5 5 L9 1" fill="none" stroke="#333" stroke-width="1.5"/></svg>
</div>
<svg class="abs" style="left:483px;top:695px" width="44" height="18" viewBox="0 0 44 18" aria-hidden="true">
  <path d="M1 5 H27 V1 L42 9 L27 17 V13 H1 Z" fill="none" stroke="#222" stroke-width="1.6" stroke-linejoin="round"/>
  <path d="M6 6 V12 M11 6 V12 M16 6 V12 M21 6 V12" stroke="#222" stroke-width="1.8"/>
</svg>
<svg class="abs" style="left:649px;top:677px" width="44" height="44" viewBox="0 0 44 44" aria-hidden="true">
  <circle cx="22" cy="22" r="21" fill="#e8393b"/>
  <path d="M12 22 L19 30 L33 14" fill="none" stroke="#fff" stroke-width="5" stroke-linecap="round" stroke-linejoin="round"/>
</svg>
<div class="abs step-pay">AND PAY THE LOWEST COST</div>

<div class="abs rule" style="top:790px"></div>
<h2 class="abs heading section-title" style="top:811px">3: OUR SELECTING USED PRINTER</h2>

<div class="abs corner-dark"></div>
<div class="abs corner-red"></div>
<article class="abs card">
  <div class="abs printer-media" role="img" aria-label="Blue and black office printer with paper"></div>
  <h3 class="abs heading card-heading">STORY BOARD</h3>
  <p class="abs copy card-copy">Crumb Corner sprouted from a hot dog cart in Linden Row Park in Eastvale created by Tomas Revel's Harbor Lane Hospitality Group (HLHG) to support the Linden Row Park Conservancy's first art installation. The cart was quite the success, with Crumb Fans lined up daily for three summers.</p>
</article>

<div class="abs footer-rule"></div>
<footer class="abs footer">ALLRIGHTS RESERVED BY <span class="red">COMPANY NAME</span>@THE DATE</footer>

</body>
</html>
```